New Business Card Design Project

Need a design that will create an impact / strong impression towards our clients for our business. We are in the lighting business and we do lighting retrofits for large commercial to industrial clientele.

Target Market(s)

Lighting Industry

Industry/Entity Type

Business

Font styles to use
Other font styles liked:
• we would like to use the font on our logo, not sure what it is though..

Requirements
Must have
• Our logo.
Nice to have
• We are open to suggestions that have to do with lighting.

```html
<!DOCTYPE html>
<html lang="en">
<head>
<meta charset="utf-8">
<title>Brightwell Retrofit Co. – Business Cards</title>
<link href="https://fonts.googleapis.com/css2?family=Open+Sans:wght@400;600;700&display=swap" rel="stylesheet">
<style>
  :root {
    --bg: #e6e8e6;
    --forest: #1d3d21;
    --back-green: #1f4722;
    --leaf: #6cc24a;
    --mid-green: #2e7d32;
    --ink: #3a3a3a;
    --paper: #ffffff;
  }
  * { margin: 0; padding: 0; box-sizing: border-box; }
  html, body { width: 1200px; height: 864px; overflow: hidden; }
  body {
    background: var(--bg);
    font-family: "Open Sans", Arial, sans-serif;
    position: relative;
  }
  .card {
    position: absolute;
    width: 600px;
    height: 343px;
    box-shadow: 0 14px 30px rgba(0,0,0,0.22);
    overflow: hidden;
  }
  .card-back {
    left: 90px; top: 50px;
    background: var(--back-green);
    display: flex; align-items: center; justify-content: center;
  }
  .brand {
    display: flex; align-items: center; gap: 12px;
    font-weight: 700; font-size: 34px; letter-spacing: 0.5px;
  }
  .brand-mark { width: 22px; height: 22px; }
  .card-back .brand { color: var(--paper); }
  .card-back .brand-mark { background: var(--paper); }

  .card-front {
    left: 510px; top: 470px;
    background: var(--paper);
  }
  .card-front .brand {
    position: absolute; left: 36px; top: 46px;
    color: var(--forest); font-size: 26px;
  }
  .card-front .brand-mark { background: var(--leaf); width: 18px; height: 18px; }
  .name-band {
    position: absolute; left: 0; top: 138px;
    width: 496px; height: 84px;
    background: var(--forest);
    color: var(--paper);
    padding: 30px 0 0 38px;
  }
  .accent-square {
    position: absolute; left: 506px; top: 138px;
    width: 34px; height: 40px; background: var(--leaf);
  }
  .person-name { font-size: 21px; font-weight: 700; line-height: 1.1; }
  .person-role { font-size: 14px; font-weight: 400; }
  .contact-list {
    position: absolute; left: 38px; top: 238px;
    list-style: none; color: var(--ink); font-size: 15px; line-height: 22px;
  }
  .contact-list li { display: flex; align-items: center; gap: 8px; }
  .contact-list svg { width: 12px; height: 12px; fill: var(--mid-green); flex: none; }
  .address {
    position: absolute; right: 42px; top: 236px;
    text-align: right; color: var(--ink); font-size: 15px; line-height: 22px;
  }
</style>
</head>
<body>

<section class="card card-back">
  <div class="brand"><span class="brand-mark"></span>Brightwell Retrofit Co.</div>
</section>

<section class="card card-front">
  <div class="brand"><span class="brand-mark"></span>Brightwell Retrofit Co.</div>

  <div class="name-band">
    <div class="person-name">John Smith</div>
    <div class="person-role">President</div>
  </div>
  <div class="accent-square"></div>

  <ul class="contact-list">
    <li>
      <svg viewBox="0 0 24 24"><path d="M6.6 10.8a15 15 0 0 0 6.6 6.6l2.2-2.2a1 1 0 0 1 1-.25 11.4 11.4 0 0 0 3.6.57 1 1 0 0 1 1 1V20a1 1 0 0 1-1 1A17 17 0 0 1 3 4a1 1 0 0 1 1-1h3.5a1 1 0 0 1 1 1c0 1.25.2 2.45.57 3.6a1 1 0 0 1-.25 1z"/></svg>
      01 012-345-6789
    </li>
    <li>
      <svg viewBox="0 0 24 24"><path d="M7 1h10a2 2 0 0 1 2 2v18a2 2 0 0 1-2 2H7a2 2 0 0 1-2-2V3a2 2 0 0 1 2-2zm0 3v14h10V4zm5 15.5a1.2 1.2 0 1 0 0 2.4 1.2 1.2 0 0 0 0-2.4z"/></svg>
      01 012-345-6780
    </li>
    <li>
      <svg viewBox="0 0 24 24"><path d="M2 5h20v14H2zm2 2v.4l8 5 8-5V7zm0 2.8V17h16V9.8l-8 5z"/></svg>
      info@yourwebsite.com
    </li>
    <li>
      <svg viewBox="0 0 24 24"><path d="M12 2a10 10 0 1 0 0 20 10 10 0 0 0 0-20zm6.9 9h-3a15 15 0 0 0-1.3-5.6A8 8 0 0 1 18.9 11zM12 4c.9 1.2 1.8 3.8 1.9 7h-3.8c.1-3.2 1-5.8 1.9-7zM9.4 5.4A15 15 0 0 0 8.1 11h-3a8 8 0 0 1 4.3-5.6zM5.1 13h3a15 15 0 0 0 1.3 5.6A8 8 0 0 1 5.1 13zM12 20c-.9-1.2-1.8-3.8-1.9-7h3.8c-.1 3.2-1 5.8-1.9 7zm2.6-1.4a15 15 0 0 0 1.3-5.6h3a8 8 0 0 1-4.3 5.6z"/></svg>
      yourwebsite.com
    </li>
  </ul>

  <address class="address" style="font-style: normal;">
    Street Name, Suite 100<br>
    State, Zip Code, Country
  </address>
</section>

</body>
</html>
```